Lantern Cove Summer Camps Banner Ads

Seeking to create 6 banner ads (two variations of 3 banner sizes. 1) 250x250 2)468x60 3)120x600.
We are a Spanish and French immersion summer camp based in Chapel Hill, North Carolina. You can view our website at http://lanterncove-example.org
We've included our logo attached, colors should be reflective of branded colors in the logo.
Our target market is the South East, United State (FL, GA, NC, SC, TN, VA). Parents (focus on mothers) with kids from grades 1-12 (ages 5-17).
Our calls to action are to register/sign up for camps, and explore our website (Goal is clicks not views).
Language for ad: English.
Final design should be a fun, family-centric ad, which encapsulates the user and encourages them to learn more about Lantern Cove. Preferably, ad can be used ever-green for reuse in different seasons (does not contain date restrictions, for example ad should NOT contain "Join us for Summer Camp 2018").
Typical tag lines include: Friends, languages and a lot of fun! All the fun of a summer camp while totally immersed in the language and culture!
Target Market(s)

```html
<!DOCTYPE html>
<html lang="en">
<head>
<meta charset="utf-8">
<title>Lantern Cove Summer Camps – Banner Ads</title>
<link rel="stylesheet" href="https://fonts.googleapis.com/css2?family=Oswald:wght@400;500;600&family=Open+Sans:wght@600;700;800&display=swap">
<style>
  :root {
    --stage: #606060;
    --paper: #ffffff;
    --brand-green: #10a68b;
    --brand-blue: #3a78c6;
    --ink: #111111;
    --button-edge: #1c3b33;
    --photo-warm: #8a7a5a;
    --photo-cool: #c9d3c8;
  }
  * { box-sizing: border-box; margin: 0; padding: 0; }
  html, body { width: 1191px; height: 1200px; overflow: hidden; }
  body { background: var(--stage); position: relative; font-family: "Open Sans", sans-serif; color: var(--ink); }

  .ad { position: absolute; background: var(--paper); overflow: hidden; }
  .ad-art { position: absolute; left: 0; top: 0; }
  .brand-name {
    position: absolute; color: var(--paper); font-family: "Open Sans", sans-serif;
    font-weight: 700; white-space: nowrap; transform-origin: left top;
  }
  .headline { font-family: "Oswald", sans-serif; font-weight: 600; color: var(--brand-green); line-height: 1; letter-spacing: -0.3px; white-space: nowrap; }
  .subhead { font-family: "Oswald", sans-serif; font-weight: 400; color: var(--ink); line-height: 1.15; white-space: nowrap; }
  .tagline { font-weight: 600; color: var(--ink); }
  .sign-up {
    position: absolute; display: flex; align-items: center; justify-content: center; gap: 8px;
    background: var(--brand-green); border: 1.5px solid var(--button-edge); border-radius: 3px;
    color: var(--paper); font-weight: 700; letter-spacing: 2px; text-decoration: none;
  }
  .sign-up svg { fill: var(--paper); }
  .site-url { position: absolute; font-weight: 700; letter-spacing: 1px; color: var(--ink); white-space: nowrap; }

  /* 120x600 skyscraper */
  .ad-skyscraper { left: 80px; top: 78px; width: 195px; height: 976px; }
  .ad-skyscraper .copy { position: absolute; left: 0; right: 0; top: 510px; text-align: center; }
  .ad-skyscraper .headline { font-size: 36px; line-height: 40px; }
  .ad-skyscraper .subhead { font-size: 29px; margin-top: 12px; line-height: 34px; }
  .ad-skyscraper .rule { width: 76px; height: 3px; background: #333; margin: 26px auto 0; }
  .ad-skyscraper .tagline { font-size: 18px; line-height: 24px; margin-top: 34px; }
  .ad-skyscraper .sign-up { left: 16px; top: 868px; width: 166px; height: 42px; font-size: 20px; }
  .ad-skyscraper .site-url { left: 0; right: 0; top: 934px; text-align: center; font-size: 11.5px; letter-spacing: 0.8px; }

  /* 250x250 square */
  .ad-square { left: 374px; top: 78px; width: 407px; height: 407px; }
  .ad-square .copy { position: absolute; left: 20px; top: 220px; }
  .ad-square .headline { font-size: 30px; }
  .ad-square .subhead { font-size: 21px; margin-top: 4px; }
  .ad-square .tagline { font-size: 14.5px; line-height: 18px; margin-top: 16px; }
  .ad-square .sign-up { left: 18px; top: 350px; width: 162px; height: 41px; font-size: 19px; }
  .ad-square .site-url { left: 228px; width: 170px; top: 365px; text-align: center; font-size: 11px; letter-spacing: 0.6px; }

  /* 468x60 leaderboard */
  .ad-leaderboard { left: 374px; top: 541px; width: 762px; height: 98px; }
  .ad-leaderboard .copy { position: absolute; left: 247px; top: 24px; text-align: center; }
  .ad-leaderboard .headline { font-size: 25px; }
  .ad-leaderboard .subhead { font-size: 16px; margin-top: 3px; }
  .ad-leaderboard .tagline { position: absolute; left: 485px; top: 22px; width: 108px; text-align: center; font-size: 13px; line-height: 17.5px; }
  .ad-leaderboard .sign-up { left: 608px; top: 27px; width: 126px; height: 32px; font-size: 16px; gap: 6px; }
  .ad-leaderboard .site-url { left: 596px; width: 150px; top: 68px; text-align: center; font-size: 9.5px; letter-spacing: 0.4px; }
</style>
</head>
<body>

<section class="ad ad-skyscraper" aria-label="Lantern Cove vertical banner">
  <svg class="ad-art" width="195" height="480" viewBox="0 0 195 480">
    <defs>
      <linearGradient id="sky-photo" x1="0" y1="0" x2="0" y2="1">
        <stop offset="0" stop-color="#4f6a3a"/>
        <stop offset="0.3" stop-color="var(--photo-cool)"/>
        <stop offset="1" stop-color="var(--photo-warm)"/>
      </linearGradient>
    </defs>
    <polygon role="img" aria-label="Photo of smiling campers in camp shirts with their counsellor" points="0,0 195,0 195,474 0,433" fill="url(#sky-photo)"/>
    <polygon points="0,430 195,470 195,478 0,438" fill="var(--brand-blue)"/>
    <polygon points="0,0 118,0 0,66" fill="var(--brand-blue)"/>
  </svg>
  <span class="brand-name" style="left:12px;top:50px;font-size:11px;transform:rotate(-29deg);">Lantern Cove</span>
  <div class="copy">
    <h2 class="headline">LANGUAGE<br>IMMERSION</h2>
    <p class="subhead">Summer and<br>Break Camps</p>
    <div class="rule"></div>
    <p class="tagline">Friends,<br>Languages and<br>a Lot of Fun!</p>
  </div>
  <a class="sign-up" href="http://lanterncove-example.org"><svg width="9" height="12" viewBox="0 0 9 12"><polygon points="0,0 9,6 0,12"/></svg>SIGN UP</a>
  <p class="site-url">lanterncove-example.org</p>
</section>

<section class="ad ad-square" aria-label="Lantern Cove square banner">
  <svg class="ad-art" width="407" height="240" viewBox="0 0 407 240">
    <defs>
      <linearGradient id="square-photo" x1="0" y1="0" x2="0" y2="1">
        <stop offset="0" stop-color="#c07ab8"/>
        <stop offset="0.25" stop-color="#8d7b5f"/>
        <stop offset="1" stop-color="#d9d6cf"/>
      </linearGradient>
    </defs>
    <polygon role="img" aria-label="Photo of a group of campers under colourful paper flags" points="0,0 407,0 407,234 0,130" fill="url(#square-photo)"/>
    <polygon points="0,124 407,228 407,237 0,133" fill="var(--brand-blue)"/>
    <polygon points="0,0 152,0 0,140" fill="var(--brand-blue)"/>
  </svg>
  <span class="brand-name" style="left:14px;top:82px;font-size:14px;transform:rotate(-36deg);">Lantern Cove</span>
  <div class="copy">
    <h2 class="headline">LANGUAGE IMMERSION</h2>
    <p class="subhead">Summer and Break Camps</p>
    <p class="tagline">All the fun of a summer camp while totally<br>immersed in the language and culture!</p>
  </div>
  <a class="sign-up" href="http://lanterncove-example.org"><svg width="9" height="12" viewBox="0 0 9 12"><polygon points="0,0 9,6 0,12"/></svg>SIGN UP</a>
  <p class="site-url">lanterncove-example.org</p>
</section>

<section class="ad ad-leaderboard" aria-label="Lantern Cove horizontal banner">
  <svg class="ad-art" width="240" height="98" viewBox="0 0 240 98">
    <defs>
      <linearGradient id="board-photo" x1="0" y1="0" x2="1" y2="1">
        <stop offset="0" stop-color="#6c86a8"/>
        <stop offset="0.5" stop-color="#7fb39a"/>
        <stop offset="1" stop-color="#a07b4e"/>
      </linearGradient>
    </defs>
    <polygon role="img" aria-label="Photo of cheering campers in a decorated room" points="0,0 234,0 216,98 0,98" fill="url(#board-photo)"/>
    <polygon points="234,0 240,0 222,98 216,98" fill="var(--brand-blue)"/>
    <polygon points="0,48 82,98 0,98" fill="var(--brand-blue)"/>
  </svg>
  <span class="brand-name" style="left:4px;top:74px;font-size:8px;">Lantern Cove</span>
  <div class="copy">
    <h2 class="headline">LANGUAGE IMMERSION</h2>
    <p class="subhead">Summer and Break Camps</p>
  </div>
  <p class="tagline">Friends,<br>Languages and<br>a Lot of Fun!</p>
  <a class="sign-up" href="http://lanterncove-example.org"><svg width="7" height="10" viewBox="0 0 9 12"><polygon points="0,0 9,6 0,12"/></svg>SIGN UP</a>
  <p class="site-url">lanterncove-example.org</p>
</section>

</body>
</html>
```